Request for Business Card Design

Hi. My name is Marlene, I am looking for a new business card design for my company, Quarrow Signal Instruments, LLC. I really like the design you did for Tarsel Venture and was hoping you could do something similar using our full logo and our mark. I am also open to any raised texture design using our mark. I have attached our full logo, which would need to be somewhere on the card, as well as the mark in both outline and full form, as well as our brand colors / guide. The card does not have to be white, as long as our logo and mark appear. I actually like darker colored business cards more, but am open to all options. If you are interested in working with me, please let me know. We would also take the business card design into letterhead design if you can do that.

```html
<!DOCTYPE html>
<html lang="en">
<head>
<meta charset="utf-8">
<title>Quarrow Signal Instruments – Business Card</title>
<link href="https://fonts.googleapis.com/css2?family=Open+Sans:wght@400;600;700&display=swap" rel="stylesheet">
<style>
  :root {
    --stage: #232326;
    --card: #1d1e21;
    --card-deep: #16171a;
    --sheen: #4a4b50;
    --brand-blue: #1a9bc9;
    --ink-light: #f2f3f5;
    --ink-muted: #8a8c92;
  }
  * { box-sizing: border-box; margin: 0; padding: 0; }
  html, body {
    width: 1200px; height: 780px; overflow: hidden;
    background: var(--stage);
    font-family: "Open Sans", sans-serif;
  }
  .canvas {
    position: relative; width: 1200px; height: 780px;
    display: flex; align-items: center; justify-content: center; gap: 40px;
  }
  .card {
    position: relative; width: 540px; height: 310px;
    border-radius: 6px; overflow: hidden;
    background: var(--card);
    box-shadow: 0 18px 40px rgba(0,0,0,.55);
  }

  /* Back side */
  .card-back__texture {
    position: absolute; inset: 0;
    background: linear-gradient(160deg, var(--sheen) 0%, #2a2b2f 28%, var(--card-deep) 55%, var(--card-deep) 100%);
  }
  .card-back__brand {
    position: absolute; right: 34px; bottom: 34px;
    display: flex; align-items: center; gap: 8px;
  }
  .brand-dot {
    width: 16px; height: 16px; border-radius: 50%;
    background: var(--brand-blue);
  }
  .card-back__name {
    font-weight: 700; font-size: 12px; letter-spacing: .06em;
    color: var(--ink-muted); text-transform: uppercase;
  }

  /* Front side */
  .card-front__brand {
    position: absolute; left: 30px; top: 34px;
    display: flex; align-items: center; gap: 12px;
  }
  .card-front__brand .brand-dot { width: 40px; height: 40px; }
  .card-front__name {
    font-weight: 700; font-size: 17px; letter-spacing: .05em;
    color: var(--ink-light); text-transform: uppercase;
  }
  .card-front__accent {
    position: absolute; right: 0; top: 74px;
    width: 14px; height: 40px; background: var(--brand-blue);
  }
  .holder {
    position: absolute; right: 30px; top: 68px; text-align: right;
  }
  .holder__name {
    font-weight: 700; font-size: 34px; line-height: 1;
    color: var(--brand-blue);
  }
  .holder__role {
    font-size: 13px; color: var(--ink-light); margin-top: 2px;
  }
  .address {
    position: absolute; left: 48px; top: 150px;
    font-size: 13px; line-height: 1.35; color: var(--ink-light);
  }
  .contact {
    position: absolute; left: 48px; top: 208px;
    list-style: none; font-size: 13px; line-height: 1.35; color: var(--ink-light);
  }
  .contact li { display: flex; align-items: center; gap: 8px; }
  .contact svg { width: 11px; height: 11px; fill: var(--brand-blue); flex: none; }
</style>
</head>
<body>
<main class="canvas">

  <section class="card card-back" aria-label="Card back">
    <div class="card-back__texture" role="img" aria-label="Raised repeating brand-mark texture on a dark card with a soft metallic sheen"></div>
    <div class="card-back__brand">
      <span class="brand-dot"></span>
      <span class="card-back__name">Quarrow Signal Instruments</span>
    </div>
  </section>

  <section class="card card-front" aria-label="Card front">
    <div class="card-front__brand">
      <span class="brand-dot"></span>
      <span class="card-front__name">Quarrow Signal Instruments</span>
    </div>

    <span class="card-front__accent"></span>
    <div class="holder">
      <p class="holder__name">Marlene</p>
      <p class="holder__role">Director</p>
    </div>

    <address class="address">
      1180 Halden Ridge Road<br>
      Fairmoor, CO 80419
    </address>

    <ul class="contact">
      <li>
        <svg viewBox="0 0 12 12" aria-hidden="true"><path d="M2.5 1 4.5 3 3.6 4.3a7 7 0 0 0 4.1 4.1L9 7.5l2 2-1.4 1.4C5.6 11 1 6.4 1.1 2.4z"/></svg>
        +001 555 218 4406
      </li>
      <li>
        <svg viewBox="0 0 12 12" aria-hidden="true"><rect x="3" y="1" width="6" height="4"/><rect x="1" y="5" width="10" height="5" rx="1"/><rect x="3" y="10" width="6" height="1.5"/></svg>
        +001 555 218 4471
      </li>
      <li>
        <svg viewBox="0 0 12 12" aria-hidden="true"><path d="M6 .5a5.5 5.5 0 1 0 0 11 5.5 5.5 0 0 0 0-11zm0 1.3c.7.8 1.2 2 1.3 3.5H4.7C4.8 3.8 5.3 2.6 6 1.8zM4.7 6.7h2.6c-.1 1.5-.6 2.7-1.3 3.5-.7-.8-1.2-2-1.3-3.5z"/></svg>
        www.quarrowsignal.com
      </li>
      <li>
        <svg viewBox="0 0 12 12" aria-hidden="true"><path d="M1 3h10v7H1zM1.6 3.5 6 7l4.4-3.5" stroke="#1d1e21" stroke-width=".9"/></svg>
        info@quarrowsignal.com
      </li>
    </ul>
  </section>

</main>
</body>
</html>
```